Fernhale Business Card Design

We are looking for a fresh business card design for our new logo. We would like a business card that is unique but friendly. We are in the window coverings business offering blinds, shutters and shades for homes.

Target Market(s)

Targeting the end-consumer

Industry/Entity Type

Business

Requirements
Must have
• Must have a dedicates space for a photo of our sales person. Must contain our new logo (attached).

```html
<!DOCTYPE html>
<html lang="en">
<head>
<meta charset="utf-8">
<title>Fernhale Business Card</title>
<link href="https://fonts.googleapis.com/css2?family=Work+Sans:wght@400;500;600&display=swap" rel="stylesheet">
<style>
  :root {
    --page-bg: #e4e2df;
    --card-bg: #f1f0ee;
    --ink-grey: #5a5a5a;
    --ink-soft: #777777;
    --leaf-green: #7cb84a;
    --band-dark: #4b4b4b;
    --band-text: #dcdcdc;
    --band-green: #80bd4c;
    --band-green-text: #e6f3d4;
    --photo-light: #9c8f86;
    --photo-dark: #2f2d2c;
  }
  * { margin: 0; padding: 0; box-sizing: border-box; }
  html, body {
    width: 1200px; height: 1047px; overflow: hidden;
    background: var(--page-bg);
    font-family: "Work Sans", sans-serif;
  }
  .card {
    position: absolute; left: 100px; top: 252px;
    width: 1000px; height: 543px;
    background: var(--card-bg);
    border-radius: 22px;
    overflow: hidden;
    box-shadow: 0 6px 24px rgba(0,0,0,0.12);
  }
  .brand {
    position: absolute; left: 65px; top: 52px;
    display: flex; align-items: center; gap: 22px;
  }
  .brand-mark {
    width: 100px; height: 100px;
    border: 4px solid var(--ink-grey); border-radius: 10px;
  }
  .brand-name {
    font-size: 62px; font-weight: 500; color: var(--ink-grey);
    letter-spacing: 0.5px;
  }
  .person-name {
    position: absolute; left: 65px; top: 200px;
    font-size: 28px; font-weight: 600; letter-spacing: 2px;
    color: var(--leaf-green); text-transform: uppercase;
  }
  .person-role {
    position: absolute; left: 65px; top: 236px;
    font-size: 21px; letter-spacing: 1.5px; color: var(--ink-soft);
    text-transform: uppercase;
  }
  .contact-band {
    position: absolute; left: 0; top: 294px; width: 100%; height: 249px;
  }
  .contact-list {
    position: absolute; left: 65px; top: 310px; list-style: none;
  }
  .contact-list li {
    display: flex; align-items: center; gap: 18px;
    height: 31.5px; font-size: 20px; color: var(--band-text);
    letter-spacing: 0.5px;
  }
  .contact-list svg { width: 20px; height: 20px; fill: var(--band-text); flex: none; }
  .address {
    position: absolute; left: 55px; top: 481px;
    font-size: 19px; letter-spacing: 0.5px; color: var(--band-green-text);
  }
  .staff-photo {
    position: absolute; left: 555px; top: 25px; width: 410px; height: 518px;
    background: linear-gradient(180deg, var(--photo-light) 0%, #6b5c52 35%, var(--photo-dark) 60%, var(--photo-dark) 100%);
    clip-path: polygon(30% 0, 70% 0, 78% 38%, 100% 48%, 100% 100%, 0 100%, 6% 48%, 22% 38%);
  }
</style>
</head>
<body>
  <div class="card">
    <svg class="contact-band" viewBox="0 0 1000 249" preserveAspectRatio="none" aria-hidden="true">
      <path d="M0 0 H628 L560 183 H0 Z" fill="var(--band-dark)"/>
      <rect x="0" y="183" width="560" height="36" fill="var(--band-green)"/>
      <rect x="0" y="219" width="560" height="30" fill="var(--band-dark)"/>
    </svg>

    <div class="brand">
      <div class="brand-mark"></div>
      <span class="brand-name">Fernhale</span>
    </div>

    <p class="person-name">Dana Mercer</p>
    <p class="person-role">Realtor</p>

    <ul class="contact-list">
      <li><svg viewBox="0 0 24 24"><path d="M6.6 10.8a15.2 15.2 0 0 0 6.6 6.6l2.2-2.2a1 1 0 0 1 1-.25 11.4 11.4 0 0 0 3.6.57 1 1 0 0 1 1 1V20a1 1 0 0 1-1 1A17 17 0 0 1 3 4a1 1 0 0 1 1-1h3.5a1 1 0 0 1 1 1c0 1.25.2 2.45.57 3.6a1 1 0 0 1-.25 1z"/></svg>(012) 555-0147</li>
      <li><svg viewBox="0 0 24 24"><path d="M7 1h10a2 2 0 0 1 2 2v18a2 2 0 0 1-2 2H7a2 2 0 0 1-2-2V3a2 2 0 0 1 2-2zm0 3v14h10V4zm5 15.5a1.2 1.2 0 1 0 0 2.4 1.2 1.2 0 0 0 0-2.4z"/></svg>(012) 555-0148</li>
      <li><svg viewBox="0 0 24 24"><path d="M6 2h12v5H6zM3 8h18a2 2 0 0 1 2 2v7h-4v5H5v-5H1v-7a2 2 0 0 1 2-2zm4 7v5h10v-5z"/></svg>(012) 555-0149</li>
      <li><svg viewBox="0 0 24 24"><path d="M2 5h20v14H2zm2 2v.5l8 5 8-5V7zm0 3v7h16v-7l-8 5z"/></svg>info@fernhalehome.com</li>
      <li><svg viewBox="0 0 24 24"><path d="M12 2a10 10 0 1 0 0 20 10 10 0 0 0 0-20zm6.9 6h-3a15 15 0 0 0-1.3-3.9A8 8 0 0 1 18.9 8zM12 4c.8 1.1 1.5 2.5 1.9 4h-3.8c.4-1.5 1.1-2.9 1.9-4zM4.3 14a8 8 0 0 1 0-4h3.4a16 16 0 0 0 0 4zm.8 2h3a15 15 0 0 0 1.3 3.9A8 8 0 0 1 5.1 16zm3-8h-3a8 8 0 0 1 4.3-3.9A15 15 0 0 0 8.1 8zM12 20c-.8-1.1-1.5-2.5-1.9-4h3.8c-.4 1.5-1.1 2.9-1.9 4zm2.3-6H9.7a14 14 0 0 1 0-4h4.6a14 14 0 0 1 0 4zm.3 5.9a15 15 0 0 0 1.3-3.9h3a8 8 0 0 1-4.3 3.9zM16.3 14a16 16 0 0 0 0-4h3.4a8 8 0 0 1 0 4z"/></svg>www.fernhalehome.com</li>
    </ul>

    <p class="address">P.O.Box: 482, Harlow Vale, Ethiopia</p>

    <div class="staff-photo" role="img" aria-label="Photo of the sales person in a dark blazer, arms crossed"></div>
  </div>
</body>
</html>
```